Ferncliff Capital - Website Design

We need a website design for a new commercial real estate company called Ferncliff Capital. We're effectively commercial mortgage brokers connecting real estate investors to lenders. We need a website that is simple (not busy), elegant, professional, and user-friendly. A lot of the users will be in their 50's and less tech savvy, so a stream-lined design is best. The website will serve as a portal for lenders to review new financing opportunities, as well as for real estate investors to review terms from lenders.
Updates
Just uploaded our logo.
Target Market(s)
Commercial real estate investors and lenders
Industry/Entity Type
Real Estate
Number of Pages Required
1 page
Colors
Designer to choose colors to be used in the design.
Look and feel

```html
<!DOCTYPE html>
<html lang="en">
<head>
<meta charset="utf-8">
<title>Ferncliff Capital</title>
<link href="https://fonts.googleapis.com/css2?family=Oswald:wght@500&family=Lato:wght@700&family=Open+Sans:wght@400;600&family=Roboto:wght@400;500;700&display=swap" rel="stylesheet">
<style>
:root{
  --orange:#e4621f;
  --orange-dark:#c9521a;
  --ink:#333333;
  --text:#444444;
  --muted:#7a7a7a;
  --light:#eeeded;
  --white:#ffffff;
  --footer:#2b2b2b;
  --line:#dddddd;
}
*{margin:0;padding:0;box-sizing:border-box}
html,body{width:1200px;height:2965px;overflow:hidden}
body{position:relative;background:var(--white);font-family:"Open Sans",sans-serif;color:var(--text)}
.abs{position:absolute}

/* header */
.site-header{left:0;top:0;width:1200px;height:103px;background:var(--white)}
.brand{left:99px;top:30px;font-family:"Roboto",sans-serif;font-weight:700;font-size:28px;color:var(--ink);display:flex;align-items:center;gap:10px}
.brand-mark{width:16px;height:16px;background:var(--orange)}
.main-nav{left:474px;top:0;height:103px;display:flex}
.main-nav a{font-family:"Roboto",sans-serif;font-weight:500;font-size:15px;color:var(--ink);text-decoration:none;line-height:103px;padding:0 30px}
.main-nav a.active{background:var(--orange);color:var(--white);padding:0 27px}

/* hero */
.hero{left:0;top:103px;width:1200px;height:514px;background:linear-gradient(180deg,#8fa68a 0%,#b7c1b2 30%,#7f9a56 62%,#5f7f2f 100%)}
.hero-title{left:99px;top:196px;font-family:"Oswald",sans-serif;font-weight:500;font-size:56px;color:var(--white);letter-spacing:.5px}
.hero-lead{left:99px;top:290px;width:520px;font-size:16px;line-height:30px;color:var(--white)}
.btn-outline{left:99px;top:380px;width:114px;height:51px;border:2px solid var(--white);color:var(--white);font-size:15px;line-height:47px;text-align:center}
.hero-dots{left:99px;top:474px;display:flex;gap:6px}
.hero-dots span{width:15px;height:15px;border-radius:50%;border:2px solid var(--white)}
.hero-dots span.on{background:var(--orange)}
.services-band{left:0;top:617px;width:1200px;height:267px;background:var(--light)}

/* service cards */
.service-card{top:560px;width:320px;height:237px;background:var(--white);border-top:4px solid var(--orange);box-shadow:0 6px 14px rgba(0,0,0,.18);text-align:center}
.service-card.featured{background:var(--orange)}
.service-card svg{margin-top:22px}
.service-card h3{font-family:"Lato",sans-serif;font-weight:700;font-size:19px;color:var(--orange);margin-top:14px}
.service-card.featured h3{color:var(--white)}
.service-card p{font-size:13px;line-height:23px;color:var(--ink);padding:10px 26px 0}
.service-card.featured p{color:var(--white)}

/* welcome */
.section-title{left:0;width:1200px;text-align:center;font-family:"Lato",sans-serif;font-weight:700;font-size:28px;color:var(--orange)}
.title-rule{left:550px;width:100px;height:2px;background:var(--orange)}
.welcome-copy{left:99px;top:1050px;width:1002px;text-align:center;font-size:13.5px;line-height:23px;color:var(--text)}
.welcome-copy p+p{margin-top:17px}
.btn{top:1226px;width:99px;height:44px;color:var(--white);font-size:13px;line-height:44px;text-align:center}
.btn-primary{left:494px;background:var(--orange)}
.btn-secondary{left:607px;background:#8a8a8a}

/* split */
.split-text{left:0;top:1354px;width:599px;height:427px;background:var(--light)}
.split-text h2{position:absolute;left:99px;top:56px;width:460px;font-family:"Lato",sans-serif;font-weight:700;font-size:21px;line-height:32px;color:var(--orange)}
.split-list{position:absolute;left:99px;top:138px;width:474px;list-style:none}
.split-list li{position:relative;padding-left:24px;font-size:13px;line-height:25px;color:var(--text);margin-bottom:10px}
.split-list li svg{position:absolute;left:0;top:6px}
.split-photo{left:599px;top:1354px;width:601px;height:427px;background:linear-gradient(135deg,#b9a595 0%,#8a7d74 45%,#a8a79a 70%,#6f6b64 100%)}

/* testimonials */
.testimonial{top:2046px;width:320px;height:220px;background:var(--light);border:3px solid var(--orange);text-align:center}
.testimonial.featured{background:var(--orange);border-color:var(--orange-dark)}
.testimonial h4{font-family:"Lato",sans-serif;font-weight:700;font-size:18px;color:var(--orange);margin-top:74px}
.testimonial.featured h4{color:var(--white)}
.testimonial p{font-size:13px;line-height:23px;color:var(--ink);padding:14px 40px 0}
.testimonial.featured p{color:var(--white)}
.avatar{top:1989px;width:102px;height:102px;border-radius:50%;border:4px solid var(--white);box-shadow:0 0 0 1px #bbb;background:linear-gradient(180deg,#d8d2cc,#9a918a)}

.divider{left:99px;top:2361px;width:1002px;height:1px;background:var(--line)}
.partner{top:2410px;width:132px;height:87px;border:1px solid var(--line);background:var(--white)}
.partner span{position:absolute;left:36px;top:30px;width:60px;height:26px;background:#cfcfcf}

/* footer */
.site-footer{left:0;top:2568px;width:1200px;height:397px;background:linear-gradient(180deg,#3a3a3a 0%,#262626 60%,#1f1f1f 100%);color:var(--white)}
.footer-brand{left:0;top:88px;width:1200px;text-align:center;font-family:"Roboto",sans-serif;font-weight:700;font-size:30px}
.footer-contact{left:0;top:176px;width:1200px;display:flex;justify-content:center;gap:40px;font-family:"Roboto",sans-serif;font-size:18px}
.footer-contact div{display:flex;align-items:center;gap:12px}
.footer-contact svg{flex:none}
.footer-nav{left:0;top:256px;width:1200px;text-align:center;font-family:"Roboto",sans-serif;font-weight:500;font-size:17px}
.footer-nav span.sep{margin:0 26px}
.footer-rule{left:99px;top:315px;width:1002px;height:1px;background:#777}
.copyright{left:99px;top:344px;font-family:"Roboto",sans-serif;font-size:14px}
.social{left:907px;top:338px;display:flex;gap:10px}
.social span{width:32px;height:32px;border-radius:50%;border:2px solid var(--white)}
</style>
</head>
<body>

<header class="abs site-header">
  <div class="abs brand"><span class="brand-mark"></span>Ferncliff Capital</div>
  <nav class="abs main-nav">
    <a class="active">HOME</a><a>ABOUT US</a><a>MORTGAGE</a><a>BLOG</a><a>CONTACT US</a>
  </nav>
</header>

<section class="abs hero" role="img" aria-label="House on a green lawn with a hand holding a stack of banknotes"></section>
<h1 class="abs hero-title">FERNCLIFF CAPITAL</h1>
<p class="abs hero-lead">Harlow Finance is a local business with local knowledge and strong industry relationships.</p>
<a class="abs btn-outline">Read More</a>
<div class="abs hero-dots"><span class="on"></span><span></span><span></span><span></span><span></span></div>

<div class="abs services-band"></div>
<article class="abs service-card" style="left:99px">
  <svg width="48" height="56" viewBox="0 0 48 56" fill="none" stroke="#e4621f" stroke-width="3"><path d="M6 26 L24 10 L42 26 V46 H6 Z"/><path d="M24 20 V40 M30 24 H21 a4 4 0 0 0 0 8 h6 a4 4 0 0 1 0 8 H18"/></svg>
  <h3>COMMERCIAL MORTGAGE</h3>
  <p>Nemo enim ipsam voluptatem quia vol up tas sit aspernatur aut odit aut fugit, sed quia consequuntur.</p>
</article>
<article class="abs service-card featured" style="left:439px">
  <svg width="56" height="56" viewBox="0 0 56 56" fill="none" stroke="#ffffff" stroke-width="3"><path d="M16 24 L28 13 L40 24 V34 H16 Z"/><path d="M6 40 H18 L26 44 H38 L48 36"/></svg>
  <h3>REAL ESTATE INVESTORS</h3>
  <p>Nemo enim ipsam voluptatem quia vol up tas sit aspernatur aut odit aut fugit, sed quia consequuntur.</p>
</article>
<article class="abs service-card" style="left:779px">
  <svg width="40" height="56" viewBox="0 0 40 56" fill="none" stroke="#e4621f" stroke-width="3"><rect x="6" y="4" width="28" height="48" rx="4"/><path d="M13 30 L20 23 L27 30 V38 H13 Z"/><circle cx="20" cy="46" r="1.5"/></svg>
  <h3>LENDERS</h3>
  <p>Nemo enim ipsam voluptatem quia vol up tas sit aspernatur aut odit aut fugit, sed quia consequuntur.</p>
</article>

<h2 class="abs section-title" style="top:950px">WELCOME TO FERNCLIFF CAPITAL</h2>
<div class="abs title-rule" style="top:1009px"></div>
<div class="abs welcome-copy">
  <p>Nemo enim ipsam voluptatem quia voluptas sit aspernatur aut odit aut fugit, sed quia consequuntur magni dolores eos qui ratione voluptatem sequi nesciunt. Neque porro quisquam est, qui dolorem ipsum quia dolor sit amet, consectetur, adipisci velit, sed quia non numquam eius modi tempora incidunt ut labore et dolore magnam aliquam quaerat voluptatem.</p>
  <p>Nam libero tempore, cum soluta nobis est eligendi optio cumque nihil impedit quo minus id quod maxime placeat facere possimus, omnis voluptas assumenda est, omnis dolor repellendus.</p>
</div>
<a class="abs btn btn-primary">Read More</a>
<a class="abs btn btn-secondary">Contact Us</a>

<section class="abs split-text">
  <h2>Local real estate experts lending to local real estate investors</h2>
  <ul class="split-list">
    <li><svg width="14" height="12" viewBox="0 0 14 12" fill="none" stroke="#e4621f" stroke-width="1.6"><path d="M1 6 H12 M8 2 L12 6 L8 10"/></svg>Harlow Finance is a local business with local knowledge and strong industry relationships. A partner with a wide network who offers value added services.</li>
    <li><svg width="14" height="12" viewBox="0 0 14 12" fill="none" stroke="#e4621f" stroke-width="1.6"><path d="M1 6 H12 M8 2 L12 6 L8 10"/></svg>Harlow has an established pool of experienced investors available for your real estate investment needs.</li>
    <li><svg width="14" height="12" viewBox="0 0 14 12" fill="none" stroke="#e4621f" stroke-width="1.6"><path d="M1 6 H12 M8 2 L12 6 L8 10"/></svg>Loans offered (Fix and Flip, Commercial)</li>
    <li><svg width="14" height="12" viewBox="0 0 14 12" fill="none" stroke="#e4621f" stroke-width="1.6"><path d="M1 6 H12 M8 2 L12 6 L8 10"/></svg>Why borrow from Harlow (experts, fast approval, professional, a partner, selective, competitive rates and fees).</li>
  </ul>
</section>
<div class="abs split-photo" role="img" aria-label="Hand holding banknotes and a hand holding house keys in front of apartment buildings"></div>

<h2 class="abs section-title" style="top:1863px">WHAT CLIENT SAY</h2>
<div class="abs title-rule" style="top:1925px"></div>

<article class="abs testimonial" style="left:99px"><h4>OWEN HALE</h4><p>Nam libero tempore, cum soluta nobis est eligendi optio cumque nihil impedit quo minus id quod.</p></article>
<article class="abs testimonial featured" style="left:439px"><h4>LENA MARSH</h4><p>Nam libero tempore, cum soluta nobis est eligendi optio cumque nihil impedit quo minus id quod.</p></article>
<article class="abs testimonial" style="left:779px"><h4>PETE ROWAN</h4><p>Nam libero tempore, cum soluta nobis est eligendi optio cumque nihil impedit quo minus id quod.</p></article>
<div class="abs avatar" style="left:208px" role="img" aria-label="Portrait of client Owen Hale"></div>
<div class="abs avatar" style="left:548px" role="img" aria-label="Portrait of client Lena Marsh"></div>
<div class="abs avatar" style="left:888px" role="img" aria-label="Portrait of client Pete Rowan"></div>

<div class="abs divider"></div>
<div class="abs partner" style="left:99px"><span></span></div>
<div class="abs partner" style="left:273px"><span></span></div>
<div class="abs partner" style="left:448px"><span></span></div>
<div class="abs partner" style="left:622px"><span></span></div>
<div class="abs partner" style="left:796px"><span></span></div>
<div class="abs partner" style="left:969px"><span></span></div>

<footer class="abs site-footer" role="img" aria-label="Dark city skyline at night behind the footer">
  <div class="abs footer-brand">Ferncliff Capital</div>
  <div class="abs footer-contact">
    <div><svg width="34" height="34" viewBox="0 0 34 34" fill="none" stroke="#fff" stroke-width="2"><circle cx="17" cy="17" r="15"/><rect x="10" y="12" width="14" height="10" fill="#fff" stroke="none"/><path d="M10 12 L17 18 L24 12" stroke="#2b2b2b" stroke-width="1.5"/></svg>info@ferncliffcapital.com</div>
    <div><svg width="34" height="34" viewBox="0 0 34 34" fill="none" stroke="#fff" stroke-width="2"><circle cx="17" cy="17" r="15"/><path d="M12 10 L15 10 L16 14 L14 15.5 Q16 19 18.5 20 L20 18 L24 19 L24 22 Q20 25 15 20 Q10 15 12 10 Z" fill="#fff" stroke="none"/></svg>+180 555 0142</div>
  </div>
  <nav class="abs footer-nav">HOME<span class="sep">|</span>ABOUT US<span class="sep">|</span>MORTGAGE<span class="sep">|</span>BLOG<span class="sep">|</span>CONTACT US</nav>
  <div class="abs footer-rule"></div>
  <p class="abs copyright">Copyrights © 2017 Ferncliff Capital. All Rights Reserved</p>
  <div class="abs social"><span></span><span></span><span></span><span></span><span></span></div>
</footer>

</body>
</html>
```